Fern Lattice Table & Chair Rentals

We need a business card for a table and chair rental company. We rent tables and chairs for weddings, funerals, business events and parties. We want something that looks clean and elegant while not being too busy. We would like colors in the green and blue hues and avoiding anything orange. We want to make sure the font is large enough to be seen easily.

Target Market(s)

Wedding & Event Rentals

Industry/Entity Type

Events

Contact Information for Business Card

Fern Lattice, sales@fernlatticerentals.com, fernlatticerentals.com, 360-555-0182

Requirements
Must have
• Easy to read font
Should not have
• Orange anywhere in the design

```html
<!DOCTYPE html>
<html lang="en">
<head>
<meta charset="utf-8">
<title>Fern Lattice Table &amp; Chair Rentals – Business Card</title>
<link href="https://fonts.googleapis.com/css2?family=Arimo:wght@400;700&display=swap" rel="stylesheet">
<style>
  :root {
    --backdrop: #e6e9e8;
    --card: #ffffff;
    --card-shade: #f0f2f2;
    --frame: #1f7a6c;
    --band-start: #3f9e6e;
    --band-end: #1c5f8a;
    --ink: #1c1c1c;
    --band-ink: #ffffff;
    --divider: rgba(255,255,255,0.75);
  }
  * { box-sizing: border-box; margin: 0; padding: 0; }
  html, body {
    width: 1200px; height: 902px; overflow: hidden;
    background: var(--backdrop);
    font-family: "Arimo", Arial, sans-serif;
    color: var(--ink);
  }
  .canvas {
    width: 1200px; height: 902px;
    display: flex; flex-direction: column;
    align-items: center; justify-content: center;
    gap: 30px;
  }
  .card {
    position: relative;
    width: 720px; height: 411px;
    background: radial-gradient(ellipse at 60% 30%, var(--card) 40%, var(--card-shade) 100%);
    box-shadow: 0 3px 10px rgba(0,0,0,0.18);
  }
  .card-frame {
    position: absolute; inset: 18px;
    border: 2px solid var(--frame);
  }
  .band {
    position: absolute; left: 26px; right: 26px; bottom: 26px;
    height: 54px;
    background: linear-gradient(90deg, var(--band-start), var(--band-end));
    display: flex; align-items: center;
    font-size: 19px; color: var(--band-ink);
  }
  .wordmark {
    font-weight: 700;
    color: var(--ink);
    line-height: 1;
    letter-spacing: -1px;
    white-space: nowrap;
  }
  .tagline {
    font-weight: 400;
    color: var(--ink);
    white-space: nowrap;
  }

  /* Front */
  .card-front .identity {
    position: absolute; left: 110px; top: 100px;
  }
  .card-front .wordmark { font-size: 84px; }
  .card-front .tagline { font-size: 38px; margin-top: 14px; margin-left: 60px; }
  .card-front .band { justify-content: center; }

  /* Back */
  .card-back .identity {
    position: absolute; left: 0; right: 0; top: 62px; text-align: center;
  }
  .card-back .wordmark { font-size: 62px; }
  .card-back .tagline { font-size: 30px; margin-top: 10px; }
  .card-back .phone {
    position: absolute; left: 0; right: 0; top: 228px;
    text-align: center; font-size: 40px; letter-spacing: 0.5px;
  }
  .card-back .band .contact { flex: 1; text-align: center; }
  .card-back .band .divider {
    width: 1px; height: 34px; background: var(--divider);
  }
</style>
</head>
<body>
<main class="canvas">
  <section class="card card-front" aria-label="Business card front">
    <div class="card-frame"></div>
    <div class="identity">
      <div class="wordmark">Fern Lattice</div>
      <div class="tagline">Table and Chair Rentals</div>
    </div>
    <div class="band">Mon-Fri: 8am to 6pm - Saturday: 8am to 4pm - Sunday: 9am to 1pm</div>
  </section>

  <section class="card card-back" aria-label="Business card back">
    <div class="card-frame"></div>
    <div class="identity">
      <div class="wordmark">Fern Lattice</div>
      <div class="tagline">Table and Chair Rentals</div>
    </div>
    <div class="phone">360-555-0182</div>
    <div class="band">
      <span class="contact">sales@fernlatticerentals.com</span>
      <span class="divider"></span>
      <span class="contact">www.fernlatticerentals.com</span>
    </div>
  </section>
</main>
</body>
</html>
```